Coastal Learner Bureau business cards

Australian company about to start offering its services. We recruit international students to come to study English, vocational education and postgraduate courses in Australia. We help them find the institution and select the right city they want to come to Australia. We are a young, online oriented and supportive agency. Our clients are between 18 and 35 years old, mainly University students, young professionals or people with work experience. We provide much more information that any other agency offer. We administrate a Facebook group with more than 11.000 members that daily ask questions about general information when coming to Australia, while they are here and even after they leave the country

Target Market(s)

International students from South America, Central America and Europe

Industry/Entity Type

Student

Contact Information for Business Card

Tomas Bilbrea
Managing Director
tomas@kelvarin.com.au
www.kelvoria.com.au
+61 491058264
Melbourne, Australia

Font styles to use
Serif
Sans Serif

Colors

Designer to choose colors to be used in the design.

Requirements
Must have
• Horizontal design
• Standard business card size and shape. If font uses green or yellow colours, they will have to match the ones from the logo
Nice to have
• UPDATE: Use the contents of the green image to design one of the card sides. Use our logo in the background of that side as watermark.
• Passport image, or immigration stamps. A picture of the Yarra River (from Melbourne) would be cool as well.
Should not have
• Non-standard business card size and shape
• Not black as the background colour of any sides as we are not a VIP agency or a hight class service. We are orientes to young people and they like colours, pictures, something attractive.
• Vertical design
• NO YELLOW or BLACK AS THE BACKGROUND COLOUR OF ANY SIDE OF THE BIZ CARD

```html
<!DOCTYPE html>
<html lang="en">
<head>
<meta charset="utf-8">
<title>Coastal Learner Bureau business cards</title>
<link href="https://fonts.googleapis.com/css2?family=Open+Sans:wght@400;600;700&display=swap" rel="stylesheet">
<style>
  :root {
    --page: #e6e8e7;
    --green: #106b46;
    --green-light: #1a8c5c;
    --green-dark: #0b5034;
    --yellow: #dfb523;
    --card-white: #f4f4f2;
    --ink-white: #ffffff;
  }
  * { box-sizing: border-box; margin: 0; padding: 0; }
  html, body { width: 1200px; height: 900px; overflow: hidden; }
  body {
    background: var(--page);
    font-family: "Open Sans", Arial, sans-serif;
    position: relative;
  }
  .card {
    position: absolute;
    left: 250px;
    width: 700px;
    height: 400px;
    overflow: hidden;
    box-shadow: 0 6px 18px rgba(0,0,0,0.18);
  }
  .card--front {
    top: 40px;
    background: linear-gradient(135deg, var(--green-light) 0%, var(--green) 45%, var(--green-dark) 100%);
    color: var(--ink-white);
  }
  .card--back {
    top: 460px;
    background: var(--card-white);
  }
  .brand {
    position: absolute;
    left: 0; right: 0;
    display: flex;
    justify-content: center;
    align-items: center;
    gap: 14px;
    font-weight: 700;
    letter-spacing: 1px;
  }
  .brand__dot {
    width: 18px; height: 18px; border-radius: 50%;
  }
  .card--front .brand { top: 130px; font-size: 62px; color: var(--ink-white); }
  .card--front .brand__dot { background: var(--ink-white); }
  .card--back .brand { top: 90px; font-size: 54px; color: var(--green); }
  .card--back .brand__dot { background: var(--yellow); }
  .tagline {
    position: absolute;
    top: 292px; left: 0; right: 0;
    display: flex;
    align-items: center;
    justify-content: center;
    gap: 14px;
    font-size: 15px;
    font-weight: 600;
  }
  .tagline__rule {
    width: 150px; height: 1px; background: rgba(255,255,255,0.8);
  }
  .person {
    position: absolute;
    left: 0; bottom: 0;
    width: 340px; height: 150px;
    background: var(--yellow);
    color: var(--ink-white);
    padding: 32px 0 0 30px;
    font-size: 19px;
    line-height: 1.25;
  }
  .person__name { font-weight: 700; text-transform: uppercase; }
  .person__role { text-transform: uppercase; }
  .contact {
    position: absolute;
    right: 0; top: 190px;
    width: 360px; height: 125px;
    background: var(--green);
    color: var(--ink-white);
    padding: 24px 28px 0 0;
    font-size: 16px;
    line-height: 1.6;
    text-align: right;
  }
  .contact__line {
    display: flex;
    justify-content: flex-end;
    align-items: center;
    gap: 10px;
  }
  .contact__icon { width: 14px; height: 14px; flex: none; }
</style>
</head>
<body>
  <section class="card card--front" aria-label="Card front">
    <div class="brand"><span class="brand__dot"></span>Kelvoria</div>
    <p class="tagline"><span class="tagline__rule"></span>Hacemos más por ti!<span class="tagline__rule"></span></p>
  </section>

  <section class="card card--back" aria-label="Card back">
    <div class="brand"><span class="brand__dot"></span>Kelvoria</div>

    <div class="contact">
      <p class="contact__line">+61 491058264
        <svg class="contact__icon" viewBox="0 0 16 16"><path fill="#fff" d="M3 1l3 3-1.5 2a9 9 0 0 0 5.5 5.5L12 10l3 3-2 2C7 15 1 9 1 3z"/></svg>
      </p>
      <p class="contact__line">tomas@kelvarin.com.au
        <svg class="contact__icon" viewBox="0 0 16 16"><rect x="1" y="3" width="14" height="10" fill="#fff"/><path d="M1 3l7 6 7-6" fill="none" stroke="#106b46" stroke-width="1.5"/></svg>
      </p>
      <p class="contact__line">www.kelvoria.com.au
        <svg class="contact__icon" viewBox="0 0 16 16"><circle cx="8" cy="8" r="7" fill="#fff"/><path d="M1 8h14M8 1c3 3 3 11 0 14M8 1c-3 3-3 11 0 14" fill="none" stroke="#106b46" stroke-width="1"/></svg>
      </p>
    </div>

    <div class="person">
      <p class="person__name">Tomas Bilbrea</p>
      <p class="person__role">Managing Director</p>
      <p class="person__place">Melbourne, Australia</p>
    </div>
  </section>
</body>
</html>
```